Brightway Haul & Upkeep Services, are a company that offers a 'one stop shop' pre-move clean up a

I have already selected a logo which I would like on the front of the business cards along with phone numbers, web address and email which are:
0487650392
www.brightwayhaul.com.au
brightwayhaulandupkeep@mailbox.example

On the back of the card I would like to list some of the types of service we offer (clean - move - repairs/maintenance) which are:
CLEAN - windows, gutters, solar panels, driveways/paths, carpets.
MOVE - Small/medium size house/office moves, large item pick-up & delivery, yard clean-up and removal.
General maintenance and repairs.

I would like the blue logo on a gray background.

Thanks

```html
<!DOCTYPE html>
<html lang="en">
<head>
<meta charset="utf-8">
<title>Brightway Haul &amp; Upkeep Services – Business Card</title>
<link rel="stylesheet" href="https://fonts.googleapis.com/css2?family=Exo+2:wght@700&family=Open+Sans:wght@400&family=PT+Sans:wght@400;700&display=swap">
<style>
  :root {
    --backdrop: #e4e6e9;
    --card: #ffffff;
    --card-edge: #c9ccd1;
    --brand-blue: #2b6cb4;
    --soft-blue: #cddcec;
    --ghost-blue: #eef3f9;
    --ghost-grey: #ececec;
    --ink: #1f1f1f;
  }
  html, body {
    margin: 0;
    padding: 0;
    width: 1200px;
    height: 1101px;
    overflow: hidden;
    background: var(--backdrop);
  }
  .canvas {
    position: relative;
    width: 1200px;
    height: 1101px;
  }
  .card {
    position: absolute;
    background: var(--card);
    border: 1px solid var(--card-edge);
    overflow: hidden;
    box-sizing: border-box;
  }

  /* Front */
  .card-front { left: 51px; top: 53px; width: 821px; height: 469px; }
  .tool-art {
    position: absolute;
    left: 492px;
    top: -40px;
    width: 380px;
    height: 560px;
    border-radius: 190px 0 0 40px;
    background: linear-gradient(180deg, var(--soft-blue), #d6e3f0);
  }
  .brand-name {
    position: absolute;
    left: 34px;
    top: 128px;
    font-family: "Exo 2", sans-serif;
    font-weight: 700;
    color: var(--brand-blue);
    line-height: 1;
    margin: 0;
  }
  .brand-name .line-main { display: block; font-size: 58px; letter-spacing: 0.5px; }
  .brand-name .line-sub { display: block; font-size: 27px; margin-top: 14px; letter-spacing: 0.3px; }
  .contact-list {
    position: absolute;
    left: 29px;
    top: 307px;
    margin: 0;
    padding: 0;
    list-style: none;
    font-family: "Open Sans", sans-serif;
    font-size: 22px;
    color: var(--ink);
  }
  .contact-list li {
    display: flex;
    align-items: center;
    height: 36px;
  }
  .contact-list svg { width: 18px; height: 18px; margin-right: 9px; flex: none; }

  /* Back */
  .card-back { left: 320px; top: 565px; width: 822px; height: 469px; }
  .ghost-name {
    position: absolute;
    left: 78px;
    top: 268px;
    margin: 0;
    font-family: "Exo 2", sans-serif;
    font-weight: 700;
    color: var(--ghost-blue);
    line-height: 1;
  }
  .ghost-name .line-main { display: block; font-size: 92px; }
  .ghost-name .line-sub { display: block; font-size: 44px; margin-top: 22px; }
  .services-title {
    position: absolute;
    left: 38px;
    top: 52px;
    margin: 0;
    font-family: "PT Sans", sans-serif;
    font-weight: 700;
    font-size: 42px;
    color: var(--brand-blue);
  }
  .service-list {
    position: absolute;
    left: 38px;
    top: 128px;
    margin: 0;
    padding: 0;
    list-style: none;
    font-family: "PT Sans", sans-serif;
    font-size: 33px;
    color: var(--ink);
    line-height: 52px;
  }
  .service-row { display: flex; gap: 30px; }
  .service-item::before {
    content: "•";
    color: var(--brand-blue);
    margin-right: 12px;
  }
</style>
</head>
<body>
<main class="canvas">

  <section class="card card-front" aria-label="Card front">
    <div class="tool-art" role="img" aria-label="Large faint wrench illustration"></div>
    <h1 class="brand-name">
      <span class="line-main">BRIGHTWAY HAUL</span>
      <span class="line-sub">&amp; UPKEEP SERVICES</span>
    </h1>
    <ul class="contact-list">
      <li>
        <svg viewBox="0 0 20 20" aria-hidden="true"><circle cx="10" cy="10" r="9" fill="none" stroke="#2b6cb4" stroke-width="1.6"/><path d="M7 5.5c-1 1 -.8 3.5 1.2 5.8s4.4 3 5.6 2l-1.6-2-1.4.7c-.8-.5-1.8-1.6-2.2-2.5l.9-1.2z" fill="#2b6cb4"/></svg>
        0487650392
      </li>
      <li>
        <svg viewBox="0 0 20 20" aria-hidden="true"><circle cx="10" cy="10" r="8.5" fill="none" stroke="#2b6cb4" stroke-width="1.5"/><ellipse cx="10" cy="10" rx="3.6" ry="8.5" fill="none" stroke="#2b6cb4" stroke-width="1.2"/><path d="M1.5 10h17M3 5.5h14M3 14.5h14" stroke="#2b6cb4" stroke-width="1.1"/></svg>
        www.brightwayhaul.com.au
      </li>
      <li>
        <svg viewBox="0 0 20 20" aria-hidden="true"><rect x="1.5" y="5" width="17" height="11" fill="#2b6cb4"/><path d="M1.5 5l8.5 6.5 8.5-6.5" fill="none" stroke="#fff" stroke-width="1.3"/></svg>
        brightwayhaulandupkeep@mailbox.example
      </li>
    </ul>
  </section>

  <section class="card card-back" aria-label="Card back">
    <p class="ghost-name" aria-hidden="true">
      <span class="line-main">BRIGHTWAY HAUL</span>
      <span class="line-sub">&amp; UPKEEP SERVICES</span>
    </p>
    <h2 class="services-title">Services we offer</h2>
    <ul class="service-list">
      <li class="service-row"><span class="service-item">Clean</span><span class="service-item">Move</span></li>
      <li class="service-item">General Maintenance And Repairs.</li>
    </ul>
  </section>

</main>
</body>
</html>
```